Northway Value Bureau (Account) WP Design

We need an Account (Profile) Wordpress design to add to nvb.co.uk.

The design should be based on https://nvb.co.uk/about/. The look and feel of the menu on the left.

The logic, after login the header menu will add another page:

Before Login:
Home / About / Trading / Support /

After Login
Home / About / Trading / Support / Account (Demo) - Logout

When you click on the / Account /

"Account Profile" page is loaded where you can change the settings etc.

"Account Profile" menu on the left should look the same as in / About / (https://nvb.co.uk/about/)

We need the following sub-pages under "Account Profile"

- Profile
- Transfers
- Reports
- Security
- API Key
- Affiliates

Now looking into each page:
-
- Profile (Should be split into individual or business) a user can choose whether how he want to run his account:

[Individual]

Personal Details
First Name:
Middle Name:
Family Name:
Citizenship:
Gender:
DOB:

[Attach File] (Government Issues ID, Passport, Driving License) - Verify

Contact Information
Phone: +44 207 555 0143 - Verify
E-Mail: sample@mailbox.example - Verify

Residential Address
Address line 1:
Address line 2:
Address line 3:
City:
Postcode:
Country:

[Attach File] (Utility Bill or Bank Statement) - Verify

[Business]

Company Name:
Registration Number:

Registered Address
Address line 1:
Address line 2:
Address line 3:
City:
Postcode:
Country:

[Attach File] (Certificate of Incorporation) - Verify
[Attach File] (Memorandum & Articles of Association)
[Attach File] (Shareholder Register)

Company Contact Information
Website:

-

- Transfers (Where a user can link a bank account to deposit or withdraw funds from the account)

Transfers

Add a bank account:

Please select the country where beneficiary’s bank is domicile: [Please select]
Please select the currency you wish to make transfers in: [Please select]

Full beneficiary name:
Full beneficiary address:
Beneficiary bank name:
Beneficiary bank address:
Beneficiary Bank Identification Code (BIC)/Routing Code:
Beneficiary IBAN number/account number:

[SAVE]

Deposti funds to NVB Bank Account
Amount of currency to be received e.g. 2345.67 [Please select: USD, EUR, GBP] :
Full beneficiary name: Northway Value Bureau Limited
Full beneficiary address: Kestrel Court
7-9 Fenwick Row
London, United Kingdom
Beneficiary bank name:
Beneficiary bank address:
Beneficiary Bank Identification Code (BIC)/Routing Code: XXXXXXXXXX
Beneficiary IBAN number/account number: XXXXXXXXXXXXXXXXXXXXXXXXXX

Deposit coins to NVB Coin Account
Amount of coins to be received e.g. 2345.67 [Please select: BTC, LTC]:
NVB Coin Account: XXXXXXXXXXXXXXXXXXXXXXXXXXXXX

Applicable charges (?):
[Clear] [Continue]

Withdraw funds from NVB Bank Account
Amount of currency to be sent e.g. 2345.67 [Please select: USD, EUR, GBP] :

Withdraw coins from NVB Coin Account:
Amount of coins to be sent e.g. 2345.67 [Please select: BTC, LTC]:
Please specify you coin account: XXXXXXXXXXXXXXXXXXXXXXXXXXXXX

Applicable charges (?):
[Clear] [Continue]

-

- Reports

TBC
-

- Security

Change Password
Current Password:
New Password:
Confirm New Password:

Enable / Disable : Two-factor Authentication (SMS)

-

- API Key
TBC

-
- Affiliates

Unlimited earning potential!
You'll receive up to 10% commission on all trades made through your affiliate link.

Referral Circle Scheme
Simply apply to our program from your publisher account or click the "Join Now" button below.

Corvalent.com - Join Now

```html
<!DOCTYPE html>
<html lang="en">
<head>
<meta charset="utf-8">
<title>Northway Value Bureau — Account Profile</title>
<link rel="stylesheet" href="https://fonts.googleapis.com/css2?family=Arimo:wght@400;700&display=swap">
<style>
:root{
  --backdrop:#333333;
  --page:#ffffff;
  --brand:#0099d6;
  --brand-dark:#1a86c0;
  --ink:#222222;
  --muted:#777777;
  --line:#cfcfcf;
  --field-text:#444444;
  --placeholder:#8a8a8a;
  --btn-dark:#3a3a3a;
}
*{box-sizing:border-box;margin:0;padding:0}
html,body{width:1043px;height:1200px;overflow:hidden;background:var(--backdrop)}
body{font-family:"Arimo",Arial,sans-serif;color:var(--ink)}
.stage{position:absolute;left:0;top:0;width:1199px;height:1381px;transform:scale(0.8699);transform-origin:0 0}
.page{position:absolute;left:66px;top:0;width:1068px;height:1347px;background:var(--page)}
.abs{position:absolute}

/* header */
.brand-name{position:absolute;left:164px;top:20px;width:132px;font-size:10px;line-height:19px;letter-spacing:4.6px;text-transform:uppercase;color:var(--ink)}
.brand-rule{position:absolute;left:308px;top:12px;width:1px;height:60px;background:var(--ink)}
.brand-dot{position:absolute;left:320px;top:22px;width:14px;height:14px;border-radius:50%;background:var(--brand)}
.main-nav{position:absolute;left:320px;top:59px;font-size:11px;color:#555}
.login{position:absolute;top:36px;height:23px;border:1px solid var(--line);font-size:11px;color:var(--placeholder);padding:5px 4px}
.login .help{position:absolute;right:10px;top:3px;width:15px;height:15px;border:1px solid #bbb;border-radius:50%;font-size:9px;text-align:center;line-height:13px;color:#999}
.btn{position:absolute;top:36px;height:21px;border-radius:3px;color:#fff;font-size:10px;font-weight:700;text-align:center;line-height:21px}
.btn-login{left:933px;width:49px;background:var(--btn-dark)}
.btn-signup{left:986px;width:49px;background:var(--brand)}

/* ticker */
.ticker{position:absolute;left:66px;top:90px;width:1068px;height:44px;background:var(--brand)}
.ticker-coin{position:absolute;left:212px;top:8px;width:28px;height:28px;border:2px solid #fff;border-radius:50%}
.stat{position:absolute;top:8px;color:#fff}
.stat .label{font-size:9.5px;display:block}
.stat .value{font-size:12.5px;display:block;margin-top:3px}
.stat .value small{font-size:9px}
.sep{position:absolute;top:0;width:1px;height:44px;background:rgba(255,255,255,.55)}

/* content */
.page-title{position:absolute;left:258px;top:188px;font-size:18px;font-weight:700}
.side-nav{position:absolute;left:200px;top:232px;width:136px;text-align:right;list-style:none}
.side-nav li{font-size:14px;font-weight:700;color:var(--muted);height:28.6px}
.side-nav li.is-active{color:var(--ink)}
.side-marker{position:absolute;left:360px;top:229px;width:2px;height:23px;background:var(--ink)}

.choice{position:absolute;top:235px;font-size:13px;display:flex;align-items:center;gap:8px}
.radio{width:12px;height:12px;border:1px solid #999;border-radius:50%;position:relative}
.radio.on::after{content:"";position:absolute;left:2px;top:2px;width:6px;height:6px;border-radius:50%;background:var(--brand)}

.section-title{position:absolute;left:455px;font-size:13px;font-weight:700}
.label{}
.field-label{position:absolute;left:380px;width:165px;text-align:right;font-size:13px;line-height:25px;color:var(--ink)}
.input{position:absolute;left:563px;width:190px;height:25px;border:1px solid var(--line);font-size:12px;line-height:23px;padding-left:11px;color:var(--field-text)}
.input.placeholder{color:var(--placeholder)}
.input svg{position:absolute;right:6px;top:5px}
.verify{position:absolute;left:759px;width:66px;height:22px;background:var(--brand);color:#fff;font-size:11.5px;font-weight:700;line-height:22px}
.verify .tick{position:absolute;left:0;top:0;width:20px;height:22px;background:var(--brand-dark)}
.verify span{position:absolute;left:27px}
.phone-code{position:absolute;left:0;top:0;width:57px;height:23px;background:#eee;border-right:1px solid var(--line);padding-left:6px;font-size:11px}
.phone-flag{display:inline-block;width:13px;height:9px;background:#c8102e;border:1px solid #1f3d7a;vertical-align:middle;margin-top:-2px}

/* footer */
.footer{position:absolute;left:66px;top:1052px;width:1068px;height:295px;background:var(--brand);color:#fff}
.footer .brand-name{color:#fff;left:98px;top:41px}
.footer .brand-rule{background:#fff;left:228px;top:36px;height:60px}
.footer .brand-dot{background:#fff;left:239px;top:45px}
.legal{position:absolute;left:98px;top:110px;font-size:9.5px;line-height:13px}
.col-title{position:absolute;top:36px;font-size:19px;font-weight:700}
.col-links{position:absolute;top:70px;list-style:none;font-size:10.5px;line-height:13.5px}
.social{position:absolute;top:71px;width:25px;height:25px;border-radius:50%;background:#fff}
.tagline-art{position:absolute;left:448px;top:185px;width:510px;height:70px;background:linear-gradient(90deg,rgba(255,255,255,.18),rgba(255,255,255,.28));border-radius:4px}
</style>
</head>
<body>
<div class="stage">
  <div class="page">
  </div>

  <header>
    <div class="brand-name">Northway Value Bureau</div>
    <div class="brand-rule"></div>
    <div class="brand-dot"></div>
    <nav class="main-nav">Home · About · Trading · Support · Account (Demo) - Logout</nav>
    <div class="login" style="left:684px;width:117px">Email<span class="help">?</span></div>
    <div class="login" style="left:808px;width:117px">Password<span class="help">?</span></div>
    <div class="btn btn-login">Log In</div>
    <div class="btn btn-signup">Sign Up</div>
  </header>

  <div class="ticker">
    <div class="ticker-coin" role="img" aria-label="Coin symbol"></div>
    <div class="stat" style="left:251px"><span class="label">Current Price</span><span class="value">$444.13</span></div>
    <div class="sep" style="left:329px"></div>
    <div class="stat" style="left:352px"><span class="label">Daily Change</span><span class="value">-9.54 <small>↓2.10%</small></span></div>
    <div class="sep" style="left:441px"></div>
    <div class="stat" style="left:463px"><span class="label">Day's Range</span><span class="value">$440.00 - $457.30</span></div>
    <div class="sep" style="left:590px"></div>
    <div class="stat" style="left:613px"><span class="label">Today's Open</span><span class="value">$453.57</span></div>
    <div class="sep" style="left:695px"></div>
    <div class="stat" style="left:718px"><span class="label">24h Volume</span><span class="value">7194 BTC</span></div>
  </div>

  <main>
    <h1 class="page-title">Account Profile</h1>
    <ul class="side-nav">
      <li class="is-active">Profile</li><li>Transfers</li><li>Reports</li><li>Security</li><li>API Key</li><li>Affiliates</li>
    </ul>
    <div class="side-marker"></div>

    <label class="choice" style="left:442px"><span class="radio on"></span>Individual</label>
    <label class="choice" style="left:529px"><span class="radio"></span>Business</label>

    <h2 class="section-title" style="top:275px">Personal Details</h2>
    <div class="field-label" style="top:308px">First Name:</div><div class="input" style="top:308px"></div>
    <div class="field-label" style="top:343px">Middle Name:</div><div class="input" style="top:343px"></div>
    <div class="field-label" style="top:379px">Family Name:</div><div class="input" style="top:379px"></div>
    <div class="field-label" style="top:415px">Citizenship:</div>
    <div class="input" style="top:415px"><svg width="12" height="12" viewBox="0 0 12 12"><path d="M2 4l4 4 4-4" fill="none" stroke="#555" stroke-width="1.4"/></svg></div>
    <div class="field-label" style="top:451px">Gender:</div>
    <div class="input" style="top:451px">Male<svg width="12" height="12" viewBox="0 0 12 12"><path d="M2 4l4 4 4-4" fill="none" stroke="#555" stroke-width="1.4"/></svg></div>
    <div class="field-label" style="top:487px">DOB:</div>
    <div class="input" style="top:487px">MM / DD / YYYY<svg width="13" height="13" viewBox="0 0 13 13"><rect x="1" y="2" width="11" height="10" fill="none" stroke="#777"/><path d="M1 5h11M4 7h1M6 7h1M8 7h1M4 9h1M6 9h1M8 9h1" stroke="#777"/></svg></div>
    <div class="field-label" style="top:522px">Attach File:</div>
    <div class="input" style="top:522px">Government Issues ID<svg width="12" height="12" viewBox="0 0 12 12"><path d="M2 4l4 4 4-4" fill="none" stroke="#555" stroke-width="1.4"/></svg></div>
    <div class="input" style="top:557px"><svg width="15" height="14" viewBox="0 0 15 14"><path d="M9 3L4 8a1.6 1.6 0 0 0 2.3 2.3L11 5.5a2.8 2.8 0 0 0-4-4L2.5 6" fill="none" stroke="#888"/><path d="M12 10h3M13.5 8.5v3" stroke="#888"/></svg></div>
    <div class="verify" style="top:559px"><i class="tick"><svg width="20" height="22" viewBox="0 0 20 22"><path d="M5 11l3.5 3.5L15 8" fill="none" stroke="#fff" stroke-width="1.6"/></svg></i><span>Verify</span></div>

    <h2 class="section-title" style="top:605px">Contact Information</h2>
    <div class="field-label" style="top:637px">Phone:</div>
    <div class="input" style="top:637px;padding-left:65px"><span class="phone-code"><i class="phone-flag"></i> +44 ⌄</span>207 555 0143</div>
    <div class="verify" style="top:639px"><i class="tick"><svg width="20" height="22" viewBox="0 0 20 22"><path d="M5 11l3.5 3.5L15 8" fill="none" stroke="#fff" stroke-width="1.6"/></svg></i><span>Verify</span></div>
    <div class="field-label" style="top:673px">E-Mail:</div>
    <div class="input placeholder" style="top:673px">sample@mailbox.example</div>
    <div class="verify" style="top:675px"><i class="tick"><svg width="20" height="22" viewBox="0 0 20 22"><path d="M5 11l3.5 3.5L15 8" fill="none" stroke="#fff" stroke-width="1.6"/></svg></i><span>Verify</span></div>

    <h2 class="section-title" style="top:719px">Residential Address</h2>
    <div class="field-label" style="top:753px">Address line 1:</div><div class="input" style="top:753px"></div>
    <div class="field-label" style="top:789px">Address line 2:</div><div class="input" style="top:789px"></div>
    <div class="field-label" style="top:824px">Address line 3:</div><div class="input" style="top:824px"></div>
    <div class="field-label" style="top:860px">City:</div><div class="input" style="top:860px"></div>
    <div class="field-label" style="top:895px">Postcode:</div><div class="input" style="top:895px"></div>
    <div class="field-label" style="top:931px">Country:</div>
    <div class="input" style="top:931px">United Kingdom<svg width="12" height="12" viewBox="0 0 12 12"><path d="M2 4l4 4 4-4" fill="none" stroke="#555" stroke-width="1.4"/></svg></div>
    <div class="field-label" style="top:967px">Attach File:</div>
    <div class="input placeholder" style="top:967px">Utility Bill or Bank Statement<svg width="15" height="14" viewBox="0 0 15 14"><path d="M9 3L4 8a1.6 1.6 0 0 0 2.3 2.3L11 5.5a2.8 2.8 0 0 0-4-4L2.5 6" fill="none" stroke="#888"/><path d="M12 10h3M13.5 8.5v3" stroke="#888"/></svg></div>
    <div class="verify" style="top:968px"><i class="tick"><svg width="20" height="22" viewBox="0 0 20 22"><path d="M5 11l3.5 3.5L15 8" fill="none" stroke="#fff" stroke-width="1.6"/></svg></i><span>Verify</span></div>
  </main>

  <footer class="footer">
    <div class="brand-name">Northway Value Bureau</div>
    <div class="brand-rule"></div>
    <div class="brand-dot"></div>
    <p class="legal">© 2014 Northway Value Bureau.<br>All rights reserved</p>
    <h3 class="col-title" style="left:400px">ABOUT US</h3>
    <ul class="col-links" style="left:400px"><li>Rulebook</li><li>Trading Fees</li><li>Partners</li><li>Security</li><li>Terms of Service</li><li>Privacy Policy</li><li>Latest News</li></ul>
    <h3 class="col-title" style="left:628px">SUPPORT</h3>
    <ul class="col-links" style="left:628px"><li>What is Bitcoin?</li><li>How to buy a bitcoin?</li><li>How to sell a bitcoin?</li></ul>
    <h3 class="col-title" style="left:833px">FOLLOW NVB</h3>
    <span class="social" style="left:833px" role="img" aria-label="Social link"></span>
    <span class="social" style="left:869px" role="img" aria-label="Social link"></span>
    <span class="social" style="left:905px" role="img" aria-label="Social link"></span>
    <span class="social" style="left:941px" role="img" aria-label="Social link"></span>
    <div class="tagline-art" role="img" aria-label="Hand-lettered slogan: Change the world one bitcoin at a time"></div>
  </footer>
</div>
</body>
</html>
```